Mental Health care Company in Washington DC

We are a new mental health care services provider in Washington DC. Please look at these sites.
https://brightwaterfamilysupport.com
https://www.quietharborinc.com
https://willowgate-dc.org/
https://www.tidepathdc.com
https://www.thelanternofdc.com

```html
<!DOCTYPE html>
<html lang="en">
<head>
<meta charset="utf-8">
<title>Calloway Health Services</title>
<link href="https://fonts.googleapis.com/css2?family=Roboto:ital,wght@0,400;0,500;0,700;1,400&display=swap" rel="stylesheet">
<style>
:root{
  --navy:#13264a;
  --navy-deep:#1b2a4a;
  --orange:#f27f22;
  --cyan:#cdf4f9;
  --text:#333a44;
  --muted:#555;
  --white:#fff;
  --black:#050505;
}
*{margin:0;padding:0;box-sizing:border-box}
html,body{width:1200px;height:3396px;overflow:hidden}
body{position:relative;font-family:'Roboto',sans-serif;color:var(--text);background:var(--white)}
.abs{position:absolute}
.topbar{left:0;top:0;width:1200px;height:40px;background:var(--navy-deep);border-top:4px solid var(--orange);color:var(--white);font-size:14px}
.topbar .item{position:absolute;top:8px;display:flex;align-items:center;gap:8px}
.header{left:0;top:40px;width:1200px;height:84px;background:var(--white)}
.brand{position:absolute;left:110px;top:14px;color:var(--navy);font-size:38px;font-weight:500;line-height:1}
.brand small{display:block;font-size:14px;letter-spacing:9px;color:#8a96a6;margin-top:4px;padding-left:40px}
.nav{position:absolute;top:33px;font-size:14px;color:var(--navy)}
.nav.active{color:var(--orange);text-decoration:underline}
.btn{position:absolute;display:flex;align-items:center;justify-content:center;background:var(--orange);color:var(--white);font-weight:700;border-radius:30px}
.hero{left:0;top:124px;width:1200px;height:474px;background:linear-gradient(90deg,#e8ecea 0%,#d9dfdc 35%,#b9c6cc 60%,#d6c8b8 100%)}
.hero h1{position:absolute;left:108px;top:90px;font-size:50px;line-height:61px;font-weight:700;color:var(--navy)}
.hero h1 span{color:var(--orange)}
.section-title{position:absolute;font-size:38px;font-weight:700;color:var(--navy);display:flex;align-items:center;gap:12px;white-space:nowrap}
.section-title::before,.section-title::after{content:"";width:40px;height:2px;background:var(--orange)}
.ph{position:absolute}
.about-text{left:642px;top:732px;width:450px;font-size:15px;line-height:25.7px;color:var(--text)}
.services{left:0;top:1145px;width:1200px;height:685px;background:var(--cyan)}
.card-img{position:absolute;top:1290px;width:220px;height:283px;border-radius:110px 110px 0 0}
.card-title{position:absolute;top:1594px;font-size:21px;font-weight:500;color:var(--navy)}
.card-desc{position:absolute;top:1628px;width:228px;font-size:14px;line-height:25px;color:var(--text)}
.card-desc em{font-style:italic}
.arrow{position:absolute;width:26px;height:26px;border-radius:50%;display:flex;align-items:center;justify-content:center}
.tcard{position:absolute;top:2000px;width:309px;height:268px;background:var(--white);border-radius:12px;box-shadow:0 2px 8px rgba(0,0,0,.15)}
.quote{position:absolute;top:-18px;left:22px;font-size:64px;font-weight:700;color:var(--orange);line-height:1}
.tcard p{position:absolute;left:24px;top:38px;width:270px;font-size:15px;line-height:26.5px;color:var(--text)}
.avatar{position:absolute;left:24px;top:180px;width:70px;height:70px;border-radius:50%;background:linear-gradient(135deg,#d9cfc6,#b8a99a)}
.tname{position:absolute;left:115px;top:190px;font-size:17px;font-weight:500;color:var(--navy)}
.trole{position:absolute;left:115px;top:218px;font-size:15px;color:var(--text)}
.cta{left:110px;top:2355px;width:977px;height:361px;background:linear-gradient(120deg,#2e466d,#1f3763 50%,#33507a);border-radius:170px 0 170px 0}
.partner{position:absolute;top:2851px;width:180px;height:115px;background:var(--white);box-shadow:0 2px 8px rgba(0,0,0,.15);border-radius:4px}
.partner i{position:absolute;left:60px;top:24px;width:60px;height:60px;border-radius:50%}
.footer{left:0;top:3055px;width:1200px;height:341px;background:var(--black);color:var(--white)}
.footer h4{position:absolute;top:84px;font-size:21px;font-weight:500}
.flink{position:absolute;left:566px;font-size:14px}
.flink::before{content:"";position:absolute;left:-18px;top:5px;width:7px;height:7px;border-radius:50%;background:var(--orange)}
.fcontact{position:absolute;left:875px;font-size:15px}
.ficon{position:absolute;left:845px;width:20px;height:20px;border-radius:50%;background:var(--orange)}
.social{position:absolute;top:3260px;width:20px;height:20px;border-radius:50%}
</style>
</head>
<body>

<div class="abs topbar">
  <div class="item" style="left:110px">
    <svg width="20" height="20" viewBox="0 0 20 20"><circle cx="10" cy="10" r="9" fill="#fff"/><path d="M10 5v5l3 2" stroke="#1b2a4a" stroke-width="2" fill="none"/></svg>
    Hours: M-F 8:30 a.m. – 5:00 p.m.
  </div>
  <div class="item" style="left:427px">
    <svg width="20" height="20" viewBox="0 0 20 20"><circle cx="10" cy="10" r="9" fill="#fff"/><path d="M7 5c-1 1-1 3 1 6s4 4 5 4l1-1-2-2-1 1c-1-.5-2-1.5-2.5-2.5l1-1-2-2z" fill="#1b2a4a"/></svg>
    +1 202 555 0147
  </div>
  <div class="item" style="left:1001px">
    <svg width="30" height="18" viewBox="0 0 30 18"><rect width="30" height="18" fill="#2c3e8c"/><path d="M0 0L30 18M30 0L0 18" stroke="#fff" stroke-width="3"/><path d="M0 0L30 18M30 0L0 18" stroke="#c8102e" stroke-width="1"/><path d="M15 0v18M0 9h30" stroke="#fff" stroke-width="5"/><path d="M15 0v18M0 9h30" stroke="#c8102e" stroke-width="3"/></svg>
    English
  </div>
</div>

<div class="abs header">
  <div class="brand">Calloway Health<small>SERVICES</small></div>
  <div class="nav active" style="left:525px">Home</div>
  <div class="nav" style="left:592px">About</div>
  <div class="nav" style="left:657px">Our Services</div>
  <div class="nav" style="left:767px">Teastimonials</div>
  <div class="nav" style="left:886px">Blog</div>
  <div class="btn" style="left:939px;top:13px;width:149px;height:57px;font-size:17px">Contact Us</div>
</div>

<section class="abs hero" role="img" aria-label="Photo of a caregiver in blue scrubs comforting a smiling older woman on a sofa">
  <h1>Healing <span>Minds</span><br>Empowering<br><span>Lives</span></h1>
  <div class="btn" style="left:111px;top:282px;width:234px;height:58px;font-size:17px">Make an Appointment</div>
</section>

<div class="ph" role="img" aria-label="Collage of four photos of therapy sessions and a smiling client, arranged as petals" style="left:110px;top:676px;width:470px;height:406px">
  <svg width="470" height="406" viewBox="0 0 470 406">
    <path d="M173 0h124v158H173V60a60 60 0 0 1 60-60z" fill="#e9c7c3"/>
    <path d="M0 158h173v86H60A60 60 0 0 1 0 184z" fill="#b9c2c8"/>
    <path d="M297 158h113a60 60 0 0 1 60 60v26H297z" fill="#a9bfa6"/>
    <path d="M175 244h124v102a60 60 0 0 1-60 60h-4a60 60 0 0 1-60-60z" fill="#c9d3dc"/>
  </svg>
</div>
<div class="section-title" style="left:642px;top:666px">About Us</div>
<p class="abs about-text">At Calloway Health Services, we are dedicated to providing compassionate, evidence-based mental health care to individuals and families in Washington, DC. Our mission is to create a safe, inclusive, and supportive environment where healing begins and hope is restored.<br>Our team of licensed therapists, counselors, and mental health professionals offers personalized care tailored to each client's unique needs. Whether you're navigating anxiety, depression, trauma, relationship challenges, or life transitions, we are here</p>
<div class="btn" style="left:642px;top:990px;width:140px;height:58px;font-size:17px">Read More</div>

<section class="abs services"></section>
<div class="section-title" style="left:433px;top:1218px">Our Services</div>
<div class="arrow" style="left:45px;top:1458px;background:var(--orange)"><svg width="10" height="10"><path d="M7 1L3 5l4 4" stroke="#fff" stroke-width="2" fill="none"/></svg></div>
<div class="arrow" style="left:1128px;top:1458px;background:#444"><svg width="10" height="10"><path d="M3 1l4 4-4 4" stroke="#fff" stroke-width="2" fill="none"/></svg></div>

<div class="card-img" role="img" aria-label="Photo of two doctors reviewing a laptop" style="left:112px;background:linear-gradient(180deg,#dfe3e6,#c8cfd5)"></div>
<div class="card-title" style="left:112px">Medical Services</div>
<div class="card-desc" style="left:113px">In addition to our counseling and therapy offerings, Calloway Health CareServices provides<br><em>Read More...</em></div>

<div class="card-img" role="img" aria-label="Photo of a therapist listening to a client in an armchair" style="left:363px;background:linear-gradient(180deg,#c9c6c0,#4a4a48)"></div>
<div class="card-title" style="left:363px">Individual Therapy</div>
<div class="card-desc" style="left:365px">Personalized one-on-one counseling for adults and teens to address anxiety, depression,<br><em>Read More...</em></div>

<div class="card-img" role="img" aria-label="Photo of a family of several generations looking at photos around a table" style="left:614px;top:1288px;width:224px;height:287px;border-radius:0;border:2px solid var(--orange);background:linear-gradient(180deg,#ddd2c4,#a58a6c)"></div>
<div class="card-title" style="left:614px">Family Therapy</div>
<div class="card-desc" style="left:615px">Support for families navigating parenting challenges, intergenerational conflict, or<br><em style="color:var(--orange)">Read More...</em></div>

<div class="card-img" role="img" aria-label="Photo of a smiling couple seated together" style="left:867px;background:linear-gradient(180deg,#8a8f93,#c99a4a)"></div>
<div class="card-title" style="left:867px">Couples Therapy</div>
<div class="card-desc" style="left:868px">Helping partners build healthier communication, resolve conflict, and strengthen emotional<br><em>Read More...</em></div>

<div class="section-title" style="left:434px;top:1902px">Testimonials</div>
<div class="arrow" style="left:45px;top:2109px;background:var(--orange)"><svg width="10" height="10"><path d="M7 1L3 5l4 4" stroke="#fff" stroke-width="2" fill="none"/></svg></div>
<div class="arrow" style="left:1128px;top:2109px;background:#444"><svg width="10" height="10"><path d="M3 1l4 4-4 4" stroke="#fff" stroke-width="2" fill="none"/></svg></div>

<div class="tcard" style="left:111px">
  <div class="quote">“</div>
  <p>The care I’ve received here has truly changed my life. My therapist listens without judgment and helps me see things clearly. I finally feel like I’m healing.</p>
  <div class="avatar" role="img" aria-label="Client portrait"></div>
  <div class="tname">Nora</div><div class="trole">A.B., Washington, DC</div>
</div>
<div class="tcard" style="left:446px">
  <div class="quote">“</div>
  <p>From the very first session, I felt supported and understood. The staff is professional, kind, and genuinely committed to mental wellness.</p>
  <div class="avatar" role="img" aria-label="Client portrait"></div>
  <div class="tname">J.L.,</div><div class="trole">Client</div>
</div>
<div class="tcard" style="left:781px">
  <div class="quote">“</div>
  <p>I was nervous to start therapy, but [Your Company Name] made it easy and safe. Their telehealth option was a game changer for my schedule.</p>
  <div class="avatar" role="img" aria-label="Client portrait"></div>
  <div class="tname">T.R.,</div><div class="trole">Virtual Client</div>
</div>

<section class="abs cta" role="img" aria-label="Navy-tinted photo of a cheerful group giving thumbs up">
  <div class="abs" style="left:0;top:72px;width:977px;text-align:center;color:#fff;font-size:38px;font-weight:700">We are happy to help you !</div>
  <div class="abs" style="left:0;top:157px;width:977px;text-align:center;color:#fff;font-size:15px">Whatever you're facing, we're happy to help you take the next step toward healing.</div>
  <div class="btn" style="left:388px;top:216px;width:199px;height:57px;font-size:17px">Contact Us Today</div>
</section>

<div class="section-title" style="left:446px;top:2780px">Our Partners</div>
<div class="partner" style="left:110px"><i style="background:#b8e6e2"></i></div>
<div class="partner" style="left:310px"><i style="background:#cfe3c2"></i></div>
<div class="partner" style="left:510px"><i style="background:#e7e3d2"></i></div>
<div class="partner" style="left:710px"><i style="background:#c9d8ee"></i></div>
<div class="partner" style="left:910px"><i style="background:#efd6b9"></i></div>

<footer class="abs footer">
  <div class="abs" style="left:110px;top:92px;font-size:46px;font-weight:500;line-height:1">Calloway Health</div>
  <div class="abs" style="left:150px;top:150px;font-size:16px;letter-spacing:10px">SERVICES</div>
  <h4 style="left:546px">Quick Links</h4>
  <div class="flink" style="top:130px">Home</div>
  <div class="flink" style="top:165px">About</div>
  <div class="flink" style="top:199px">Our Services</div>
  <div class="flink" style="top:233px">Testimonials</div>
  <div class="flink" style="top:267px">Blog</div>
  <h4 style="left:845px">Contact Us</h4>
  <div class="ficon" style="top:129px"></div><div class="fcontact" style="top:129px">+1 202 555 0147</div>
  <div class="ficon" style="top:163px"></div><div class="fcontact" style="top:163px">hello@callowayhealth.org</div>
  <div class="ficon" style="top:198px"></div><div class="fcontact" style="top:198px">410 Linden Row NW,</div>
  <div class="fcontact" style="top:232px">Suite 200, Washington, DC 20005</div>
  <div class="abs" style="left:110px;top:307px;width:978px;height:1px;background:#444"></div>
  <div class="abs" style="left:0;top:318px;width:1200px;text-align:center;font-size:11px">© 2025 Calloway Health Services. All rights reserved.</div>
</footer>
<div class="social" style="left:186px;background:var(--orange)"></div>
<div class="social" style="left:221px;background:#fff"></div>
<div class="social" style="left:254px;background:#fff"></div>

</body>
</html>
```